Covid 19 Exit Strategy one page brochure

I would like to design, and will need URGENT help, a brochure detailing a Covid 19 Exit Strategy plan. This brochure will need to be understood easily and the graphics inside should make it easy for people to understand without reading the entire text. This project is quite urgent and needs to be completed THIS WEEK - by Saturday may 16th at the latest. I am attaching two examples. I will provide the text.

```html
<!DOCTYPE html>
<html lang="en">
<head>
<meta charset="utf-8">
<title>Exit Strategy Flyer</title>
<link href="https://fonts.googleapis.com/css2?family=Montserrat:wght@400;500;600;700;800&display=swap" rel="stylesheet">
<style>
  :root {
    --navy: #1d3566;
    --navy-deep: #14254a;
    --red: #d3262b;
    --sky: #6fa6e0;
    --ink: #1f2430;
    --muted: #555b66;
    --rule: #c9ccd2;
    --paper: #ffffff;
    --backdrop: #e6e7e9;
  }
  * { box-sizing: border-box; margin: 0; padding: 0; }
  html, body { width: 1200px; height: 960px; overflow: hidden; }
  body {
    background: var(--backdrop);
    font-family: "Montserrat", Arial, sans-serif;
    color: var(--ink);
    position: relative;
  }
  .flyer {
    position: absolute;
    left: 280px; top: 28px;
    width: 640px; height: 904px;
    background: var(--paper);
    overflow: hidden;
    box-shadow: 0 6px 24px rgba(0,0,0,.12);
  }
  .hero {
    position: absolute; left: 0; top: 0; width: 100%; height: 330px;
    background:
      radial-gradient(circle at 78% 28%, #6d93cf 0, #3e64a5 14%, transparent 32%),
      radial-gradient(circle at 58% 18%, #5a7fbe 0, transparent 14%),
      radial-gradient(circle at 66% 62%, #4d73b3 0, transparent 12%),
      linear-gradient(135deg, var(--navy) 0%, #2a4a86 55%, var(--navy-deep) 100%);
  }
  .hero-title {
    position: absolute; left: 42px; top: 138px;
    font-weight: 800; line-height: 1.02; text-transform: uppercase;
  }
  .hero-title .line-main { color: #fff; font-size: 42px; letter-spacing: .5px; }
  .hero-title .line-accent { color: var(--red); font-size: 42px; }
  .hero-title .line-sub { color: #fff; font-size: 24px; font-weight: 700; margin-top: 10px; line-height: 1.15; }
  .hero-stripe {
    position: absolute; left: 0; top: 330px; width: 100%; height: 8px; background: var(--sky);
  }
  .banner {
    position: absolute; left: 190px; top: 292px; width: 390px; height: 58px;
    background: var(--red);
    clip-path: polygon(0 0, 100% 0, 100% 100%, 6% 100%);
    color: #fff; font-weight: 800; font-size: 34px;
    display: flex; align-items: center; justify-content: center;
    letter-spacing: .5px; padding-left: 18px;
  }
  .objective {
    position: absolute; left: 40px; right: 40px; top: 364px; text-align: center;
  }
  .objective .label { color: var(--red); font-size: 13px; font-weight: 500; letter-spacing: .5px; }
  .objective .question { font-size: 14px; font-weight: 700; margin-top: 2px; }
  .objective .aim { font-size: 15px; font-weight: 500; margin-top: 8px; line-height: 1.35; }
  .strategy-grid {
    position: absolute; left: 30px; top: 482px; width: 580px; height: 316px;
    display: grid; grid-template-columns: repeat(3, 1fr); grid-template-rows: repeat(2, 158px);
    border: 1px solid var(--rule);
  }
  .measure {
    border-right: 1px solid var(--rule); border-bottom: 1px solid var(--rule);
    display: flex; flex-direction: column; align-items: center; justify-content: center;
    text-align: center; padding: 6px 12px; gap: 7px;
    font-size: 10.5px; line-height: 1.3; color: var(--ink);
    min-height: 0;
  }
  .measure:nth-child(3n) { border-right: 0; }
  .measure:nth-child(n+4) { border-bottom: 0; }
  .measure strong { font-weight: 700; }
  .measure-icon {
    flex: none;
    width: 62px; height: 44px; border-radius: 7px;
    background: linear-gradient(135deg, #e8eef8 0%, #d7e3f4 60%, #f5dede 100%);
  }
  .info-band {
    position: absolute; left: 200px; right: 0; top: 812px; height: 46px;
    background: var(--sky); color: #fff;
    display: flex; align-items: center; justify-content: space-between;
    padding: 0 16px; gap: 12px;
  }
  .info-band .campaign { font-size: 10px; line-height: 1.3; }
  .info-band .campaign b { font-weight: 700; font-size: 11px; display: block; }
  .info-band .contact { font-size: 9.5px; line-height: 1.35; white-space: nowrap; }
  .info-band .contact b { font-weight: 700; display: block; }
  .contact-row { display: flex; gap: 10px; align-items: center; }
  .contact-row svg { width: 9px; height: 9px; vertical-align: -1px; margin-right: 3px; }
  .corner-block {
    position: absolute; left: 0; bottom: 0; width: 42px; height: 42px; background: var(--sky);
  }
  .issuer {
    position: absolute; left: 62px; bottom: 10px;
    display: flex; align-items: center; gap: 10px;
  }
  .issuer-mark { width: 14px; height: 14px; background: var(--red); }
  .issuer-divider { width: 1px; height: 30px; background: var(--rule); }
  .issuer-name {
    font-size: 8.5px; font-weight: 500; letter-spacing: .6px; color: var(--muted);
    text-transform: uppercase; line-height: 1.4;
  }
</style>
</head>
<body>
  <article class="flyer">
    <header class="hero" role="img" aria-label="Close-up micrograph of blue coronavirus particles on a dark blue background">
      <h1 class="hero-title">
        <div class="line-main">Coronavirus</div>
        <div class="line-accent">Covid-19</div>
        <div class="line-sub">Information and<br>guidelines</div>
      </h1>
    </header>
    <div class="hero-stripe"></div>
    <div class="banner">THE EXIT STRATEGY</div>

    <section class="objective">
      <p class="label">OBJECTIVE :</p>
      <p class="question">WHAT DOES THE STRATEGY CONSIST OF ?</p>
      <p class="aim">To gradually phase out the restrictions imposed to curb the spread of the coronavirus while remaining cautious.</p>
    </section>

    <section class="strategy-grid">
      <div class="measure">
        <div class="measure-icon" role="img" aria-label="Line icon of a hospital building"></div>
        <p><strong>Ensure</strong>, at<br>all times, sufficient<br><strong>hospital capacities.</strong></p>
      </div>
      <div class="measure">
        <div class="measure-icon" role="img" aria-label="Line icon of a country outline with a pandemic curve and a tick"></div>
        <p><strong>Provide close monitoring</strong> of the evolution of the pandemic during the entire exit, as well as the secondary effects of the confinement.</p>
      </div>
      <div class="measure">
        <div class="measure-icon" role="img" aria-label="Line icon of people keeping distance around a dashed circle"></div>
        <p><strong>Apply basic barrier gestures</strong> and reinforce them with other specific measures, including in the workplace, to minimize the risk of an uncontrolled spread of the virus.</p>
      </div>
      <div class="measure">
        <div class="measure-icon" role="img" aria-label="Line icon of a house with an alert sign and an arrow"></div>
        <p>Foresee the possibility of reintroducing <strong>stricter measures</strong> in the event of a strong resurgence of the virus among the population.</p>
      </div>
      <div class="measure">
        <div class="measure-icon" role="img" aria-label="Line icon of test tubes with a rising arrow"></div>
        <p><strong>Foster testing capacities</strong> and support research in particular with regard to tests to measure the acquired immunity of the population.</p>
      </div>
      <div class="measure">
        <div class="measure-icon" role="img" aria-label="Line icon of vulnerable people under a protective dashed arc"></div>
        <p><strong>Protect</strong>, in particular,<br><strong>vulnerable</strong> groups.</p>
      </div>
    </section>

    <footer>
      <div class="info-band">
        <p class="campaign"><b>#STAYSAFEHOME</b>Don't have to go outside? Please stay at home!</p>
        <div class="contact">
          <b>FOR INFORMATION</b>
          <div class="contact-row">
            <span><svg viewBox="0 0 10 10"><path d="M2 1l2 2-1 1.2c.6 1.2 1.6 2.2 2.8 2.8L7 6l2 2-1.2 1.2C4.5 9 1 5.5.8 2.2z" fill="#fff"/></svg>8000 - 1234</span>
            <span><svg viewBox="0 0 10 10"><circle cx="5" cy="5" r="4" fill="none" stroke="#fff" stroke-width="1"/><path d="M1 5h8M5 1c-2 2.5-2 5.5 0 8M5 1c2 2.5 2 5.5 0 8" fill="none" stroke="#fff" stroke-width=".8"/></svg>www.healthguide-info.org</span>
          </div>
        </div>
      </div>
      <div class="corner-block"></div>
      <div class="issuer">
        <span class="issuer-mark"></span>
        <span class="issuer-divider"></span>
        <span class="issuer-name">Office of Public Health<br>Coordination</span>
      </div>
    </footer>
  </article>
</body>
</html>
```